Redesign of outdated "Automotive Automation Company"

We are looking to finally update our outdated website with some cutting edge graphics. We want our customers to know we value technology and are cutting edge as far as design. We provide automation solutions for the automotive industry which essentially means we program robots, and sell automation related products.

Current URL

http://lnk.qorvi.example/Tm4pzr
Updates

Project Deadline Extended
Reason: The client portal wasn't working, it's just finally been fixed by Pixel Harbor. I will go through and start reviewing designs.

We are trying to go with the same look and feel on our business cards, line cards, apparel, etc. so we are forming a brand. I have included the current draft of the line card. Please utilize our newest Logo VEL Standardized Logo.jpg http://img.plomtra.example/zuKe9rb.jpg?1 Also we are trying hard to sell the following software / hardware companies so we can put some emphasis on their product. Corvane Systems https://www.corvanesystems.example/ We make money on selling the software and then on the integration. I think you should tie in this animation. ยท Shop Line Muddle to Momentum https://media.vuntelo.example/clips/9b2e7f1d04c3a85e6f2d1b7c9a0e4f3d8c6b2a1e.jpg?image_play_button=true&image_play_button_color=7b796ae0&image_crop_resized=275x155 In this 2-minute video, discover how Trellan can help run your plant floor. We are Authorized Integrators / Resellers for Pembry Controls Hadrix Sensorik http://hadrix.example/en/usa/ Corvane Systems https://www.corvanesystems.example/ Unified Motion Works www.umwkq.example Brisk Beltway Corp www.briskbeltway.example Castmere Fabrication http://www.castmerefab.example/strategic_partners.aspx

Target Market(s)

Large automotive companies looking for automation or robotic programming. So Professional is key.

Industry/Entity Type

Automotive

Font styles to use
Other font styles liked:
• Possible Open Sans or Lato

Colors
0591cc
ceeaf6
fbd4d5
fbf289
fece3e

Requirements
Must have
• Professional Modern Design.

I want a homepage design, and a rough Sales Page... Where numerous products can be listed.
Nice to have
• Maybe an updated logo if possible.

```html
<!DOCTYPE html>
<html lang="en">
<head>
<meta charset="utf-8">
<title>VEL Engineering Solutions</title>
<link href="https://fonts.googleapis.com/css2?family=Open+Sans:wght@400;600;700&display=swap" rel="stylesheet">
<style>
:root{
  --orange:#f9a31b;
  --pink:#f0145a;
  --green:#79c142;
  --blue:#1ab2e0;
  --dark:#3c3c3c;
  --text:#555;
  --soft:#f3f3f3;
  --black:#0b0b0f;
}
*{margin:0;padding:0;box-sizing:border-box}
html,body{width:806px;height:1200px;overflow:hidden}
body{font-family:"Open Sans",Arial,sans-serif;color:var(--text);background:#fff;position:relative}
.abs{position:absolute}
.topline{left:0;top:0;width:806px;height:2px;background:var(--orange)}
.call{left:108px;top:14px;display:flex;gap:9px;align-items:flex-start}
.call small{display:block;font-size:6.5px;color:#666}
.call strong{display:block;font-size:10.5px;font-weight:400;color:#555;margin-top:1px}
.nav{right:138px;top:18px;display:flex;gap:13px;font-size:6.8px;font-weight:600;color:#444}
.nav .active{color:var(--pink)}
.brand{left:306px;top:-90px;width:194px;height:198px;border-radius:50%;background:#fff;box-shadow:0 3px 5px rgba(0,0,0,.25);z-index:3;text-align:center}
.brand .name{margin-top:124px;font-size:32px;font-weight:700;color:var(--pink);line-height:1}
.brand .sub{font-size:5.4px;color:#333;letter-spacing:.3px;margin-top:6px}
.hero{left:0;top:46px;width:806px;height:432px;
  background:
    radial-gradient(ellipse 120px 150px at 330px 150px,rgba(232,196,160,.95),rgba(232,196,160,0)),
    radial-gradient(ellipse 140px 90px at 310px 40px,rgba(140,72,40,.85),rgba(140,72,40,0)),
    radial-gradient(ellipse 170px 140px at 600px 110px,rgba(160,196,222,.9),rgba(160,196,222,0)),
    radial-gradient(ellipse 90px 220px at 690px 300px,rgba(225,225,220,.9),rgba(225,225,220,0)),
    radial-gradient(ellipse 180px 130px at 450px 320px,rgba(214,196,176,.9),rgba(214,196,176,0)),
    radial-gradient(ellipse 160px 200px at 90px 250px,rgba(150,124,96,.9),rgba(150,124,96,0)),
    linear-gradient(110deg,#a58c70 0%,#d9c4a6 40%,#c9c2b4 65%,#8f9aa4 100%)}
.cap{left:108px;color:#fff;font-weight:600;padding:0 13px;display:flex;align-items:center}
.cap-1{top:228px;height:40px;background:rgba(121,193,66,.92);font-size:14px;width:244px}
.cap-2{top:271px;height:32px;background:rgba(40,40,40,.82);font-size:11.6px;width:296px;padding:0 11px}
.arrow{top:248px;width:28px;height:28px}
.cards{left:108px;top:418px;display:flex;box-shadow:0 10px 10px -6px rgba(0,0,0,.2)}
.card{width:196px;height:104px;display:flex;gap:10px;padding:18px 10px 0 10px;color:#fff}
.card h3{font-size:11.5px;font-weight:700;letter-spacing:.3px;margin:14px 0 10px}
.card p{font-size:6.8px;line-height:1.5;opacity:.9}
.card-auto{background:linear-gradient(90deg,#f4135c,#fb5a7a)}
.card-robo{background:linear-gradient(90deg,#fba20e,#fcc02e)}
.card-ctrl{background:linear-gradient(90deg,#6fbc3a,#8fd055)}
.card svg{flex:none}
.sec-title{font-size:14.5px;font-weight:700;color:var(--dark);letter-spacing:.2px}
.sec-sub{font-size:9px;color:var(--orange);margin-top:4px}
.wwd{left:109px;top:538px}
.vline{left:229px;top:548px;width:1px;height:88px;background:#e2e2e2}
.pager{left:108px;top:602px;display:flex;gap:5px}
.pager span{width:23px;height:21px;background:#f1f1f1;display:flex;align-items:center;justify-content:center;color:#ccc;font-size:10px}
.intro{left:258px;top:540px;width:440px;font-size:7.1px;line-height:1.75;color:#777}
.feat{top:600px;display:flex;gap:14px}
.feat h4{font-size:6.8px;font-weight:400;color:#444;margin:3px 0 8px}
.feat p{font-size:7px;line-height:1.6;color:#888;width:160px}
.projects{left:0;top:671px;width:806px;height:306px;background:var(--soft)}
.proj-head{left:109px;top:687px}
.proj{top:744px;width:126px}
.proj .ph{width:122px;height:92px;border:2px solid #fff;box-shadow:0 0 2px rgba(0,0,0,.2)}
.proj h5{font-size:7.8px;font-weight:600;color:#444;margin-top:9px;line-height:1.7}
.proj ul{list-style:none;margin-top:5px}
.proj li{font-size:6.8px;color:#777;line-height:1.95}
.btn{top:922px;width:64px;height:24px;color:#fff;font-size:6.6px;font-weight:700;display:flex;align-items:center;justify-content:center}
.dist-head{left:109px;top:1003px}
.partner{top:1064px;text-align:left}
.partner .pname{font-size:13px;font-weight:600;display:flex;align-items:center;gap:5px}
.partner .pcap{font-size:7.8px;color:#333;margin-top:10px}
.pdiv{top:1068px;width:1px;height:36px;background:#e3e3e3}
.footer{left:0;top:1136px;width:806px;height:60px;background:var(--black)}
.footline{left:0;top:1196px;width:806px;height:4px;background:var(--orange)}
.flinks{left:109px;top:1158px;font-size:5.8px;color:#ccc;display:flex;gap:7px}
.copy{left:109px;top:1174px;font-size:5.8px;color:#ccc}
.pay{left:403px;top:1160px;display:flex;gap:3px}
.pay span{width:29px;height:19px;border-radius:2px;background:#e9e9e9}
.pay span:nth-child(2){background:#f0b441}
.pay span:nth-child(3){background:#1d4f9c}
.pay span:nth-child(4){background:#a9bcd6}
.social{left:597px;top:1154px;display:flex;gap:6px}
.social span{width:20px;height:20px;border-radius:50%;border:1.5px solid #fff}
.c4{left:724px;top:1157px;font-size:6px;color:#ccc}
.ph-1{background:radial-gradient(ellipse 40px 30px at 95px 25px,#3d4a5c,rgba(61,74,92,0)),radial-gradient(ellipse 50px 25px at 60px 75px,#f2f2ef,rgba(242,242,239,0)),linear-gradient(135deg,#dfe4ea,#8c98a6 60%,#4c5868)}
.ph-2{background:radial-gradient(ellipse 30px 45px at 30px 45px,#2a3038,rgba(42,48,56,0)),radial-gradient(ellipse 40px 40px at 90px 40px,#c6ccd2,rgba(198,204,210,0)),linear-gradient(90deg,#3a424c,#6c7682 50%,#2f363f)}
.ph-3{background:radial-gradient(ellipse 40px 35px at 45px 45px,#8fb8dc,rgba(143,184,220,0)),radial-gradient(ellipse 30px 40px at 100px 35px,#6b4e3e,rgba(107,78,62,0)),linear-gradient(135deg,#1a3f66,#356c9c 55%,#12283f)}
.ph-4{background:radial-gradient(ellipse 60px 15px at 60px 55px,#e8a25c,rgba(232,162,92,0)),linear-gradient(180deg,#3a5aa0 0%,#8a7fa8 40%,#c98a6a 58%,#3a3a44 75%,#1c2230 100%)}
</style>
</head>
<body>
<div class="abs topline"></div>

<header>
  <div class="abs call">
    <svg width="20" height="14" viewBox="0 0 20 14"><path d="M1 5 Q10 -1 19 5 L16 7 13 5 V4 H7 V5 L4 7Z" fill="#27a84a"/><rect x="3" y="7" width="14" height="7" rx="1" fill="#27a84a"/><circle cx="10" cy="10.5" r="2" fill="#fff"/></svg>
    <div><small>CALL US:</small><strong>5550142277</strong></div>
  </div>
  <div class="abs brand">
    <div class="name">VEL</div>
    <div class="sub">ENGINEERING SOLUTIONS</div>
  </div>
  <nav class="abs nav"><span class="active">HOME PAGE</span><span>SERVICES</span><span>CONTACT</span><span>ABOUT</span></nav>
</header>

<section>
  <div class="abs hero" role="img" aria-label="Photo of an engineer adjusting a robotic arm with a screwdriver in a lab"></div>
  <div class="abs cap cap-1">YOUR PREMIER AUTOMATION</div>
  <div class="abs cap cap-2">CONSULTING &amp; SYSTEMS INTEGRATION CHOICE!</div>
  <svg class="abs arrow" style="left:11px" viewBox="0 0 28 28"><circle cx="14" cy="14" r="12.5" fill="none" stroke="#fff" stroke-width="2.5"/><path d="M16 8 L10 14 16 20" fill="none" stroke="#fff" stroke-width="2.5"/></svg>
  <svg class="abs arrow" style="left:760px" viewBox="0 0 28 28"><circle cx="14" cy="14" r="12.5" fill="none" stroke="#fff" stroke-width="2.5"/><path d="M12 8 L18 14 12 20" fill="none" stroke="#fff" stroke-width="2.5"/></svg>

  <div class="abs cards">
    <div class="card card-auto">
      <svg width="64" height="72" viewBox="0 0 64 72" fill="#fff"><circle cx="20" cy="22" r="13" fill="none" stroke="#fff" stroke-width="7" stroke-dasharray="5 3.2"/><circle cx="20" cy="22" r="10"/><circle cx="20" cy="22" r="4" fill="#f4135c"/><circle cx="46" cy="38" r="8" fill="none" stroke="#fff" stroke-width="6" stroke-dasharray="4 2.3"/><circle cx="46" cy="38" r="7"/><circle cx="46" cy="38" r="3" fill="#f4135c"/><circle cx="26" cy="56" r="8" fill="none" stroke="#fff" stroke-width="6" stroke-dasharray="4 2.3"/><circle cx="26" cy="56" r="7"/><circle cx="26" cy="56" r="3" fill="#f4135c"/></svg>
      <div><h3>AUTOMATION</h3><p>Industrial Automation is con-<br>stantly evolving with ever.</p></div>
    </div>
    <div class="card card-robo">
      <svg width="64" height="80" viewBox="0 0 64 80" fill="#fff"><rect x="30" y="0" width="4" height="5"/><rect x="22" y="5" width="20" height="15"/><circle cx="28" cy="12" r="2.5" fill="#fba20e"/><circle cx="36" cy="12" r="2.5" fill="#fba20e"/><rect x="18" y="23" width="28" height="26"/><rect x="22" y="51" width="7" height="20"/><rect x="35" y="51" width="7" height="20"/><path d="M18 26 L6 38 9 41 18 33Z"/><path d="M46 26 L58 38 55 41 46 33Z"/></svg>
      <div><h3>ROBOTICS</h3><p>Industrial Automation is con-<br>stantly evolving with ever.</p></div>
    </div>
    <div class="card card-ctrl">
      <svg width="64" height="72" viewBox="0 0 64 72"><rect x="4" y="4" width="56" height="6" fill="#fff"/><rect x="29" y="10" width="6" height="6" fill="#fff"/><path d="M8 16 Q32 10 56 16 L52 66 H12Z" fill="#fff"/><circle cx="32" cy="42" r="13" fill="#6fbc3a"/><circle cx="32" cy="42" r="10" fill="#fff"/><path d="M32 42 L37 36" stroke="#6fbc3a" stroke-width="2"/></svg>
      <div><h3>CONTROLS</h3><p>Industrial Automation is con-<br>stantly evolving with ever.</p></div>
    </div>
  </div>
</section>

<section>
  <div class="abs wwd"><h2 class="sec-title">WHAT WE DO</h2><div class="sec-sub">1-888-VEL-ROBO</div></div>
  <div class="abs pager"><span>‹</span><span>›</span></div>
  <div class="abs vline"></div>
  <p class="abs intro">Industrial Automation is constantly evolving with ever-changing technological breakthroughs. For companies to remain competitive, they need to be more nimble than ever implementing productivity and manufacturing innovations. But identifying and implementing the right Automation, Robotics and industrial Controls is never easy.</p>
  <div class="abs feat" style="left:256px">
    <svg width="32" height="32" viewBox="0 0 32 32"><path d="M4 26 L24 6 28 10 8 30Z" fill="var(--pink)"/><path d="M6 6 L26 26" stroke="var(--pink)" stroke-width="4"/></svg>
    <div><h4>APPLICATIONS ENGINEERING</h4><p>Provide electrical and mechanical expertise to solve automation specific application.</p></div>
  </div>
  <div class="abs feat" style="left:490px">
    <svg width="40" height="40" viewBox="0 0 40 40"><circle cx="20" cy="20" r="18" fill="none" stroke="var(--pink)" stroke-width="2"/><path d="M20 6 A14 14 0 0 1 34 20 H20Z" fill="var(--pink)"/></svg>
    <div><h4>CONTROLS ENGINEERING</h4><p>Provide electrical and mechanical expertise to solve automation specific application.</p></div>
  </div>
</section>

<section>
  <div class="abs projects"></div>
  <div class="abs proj-head"><h2 class="sec-title">OUR PROJECTS</h2><div class="sec-sub">HELPING YOUR BUSINESS OPTIMIZE ITS AUTOMATION....</div></div>

  <div class="abs proj" style="left:108px">
    <div class="ph ph-1" role="img" aria-label="Photo of businessmen reviewing documents at a desk"></div>
    <h5>SPECIALIZING IN THE<br>FOLLOWING AREAS</h5>
    <ul><li>• 2D and 3D Capabilities</li><li>• Automation Product Sales</li><li>• Consulting</li></ul>
  </div>
  <div class="abs proj" style="left:265px">
    <div class="ph ph-2" role="img" aria-label="Photo of a technician working on server racks"></div>
    <h5>AREAS OF EXPERTISE</h5>
    <ul><li>• HMI's</li><li>• Motion Contol</li><li>• Robotics</li></ul>
  </div>
  <div class="abs proj" style="left:421px">
    <div class="ph ph-3" role="img" aria-label="Photo of a programmer with floating binary digits"></div>
    <h5>PROGRAMMING LANGUAGES</h5>
    <ul><li>• Batch</li><li>• Java</li><li>• C++</li></ul>
  </div>
  <div class="abs proj" style="left:573px">
    <div class="ph ph-4" role="img" aria-label="Photo of an industrial plant at dusk"></div>
    <h5>INDUSTRIES</h5>
    <ul><li>• Assembly</li><li>• Distribution</li><li>• Manufacturing</li></ul>
  </div>

  <div class="abs btn" style="left:108px;background:var(--pink)">READ MORE</div>
  <div class="abs btn" style="left:265px;background:var(--orange)">READ MORE</div>
  <div class="abs btn" style="left:421px;background:var(--green)">READ MORE</div>
  <div class="abs btn" style="left:572px;background:var(--blue)">READ MORE</div>
</section>

<section>
  <div class="abs dist-head"><h2 class="sec-title">AUTHORIZED DISTRIBUTOR*</h2><div class="sec-sub">REPRESENTING THE FOLLOWING CATEGORY SPECIFIC MANUFACTURERS.</div></div>
  <div class="abs partner" style="left:109px">
    <div class="pname" style="color:#d4213d"><span style="width:10px;height:10px;background:#d4213d;display:inline-block"></span>Hadrix Sensorik</div>
    <div class="pcap">Sensors, Safety and Barcode Readers</div>
  </div>
  <div class="abs pdiv" style="left:304px"></div>
  <div class="abs partner" style="left:357px">
    <div class="pname" style="color:#4d6b3a"><span style="width:12px;height:12px;border-radius:50%;background:#4d6b3a;display:inline-block"></span>Corvane Systems</div>
    <div class="pcap" style="padding-left:8px">Software Solutions</div>
  </div>
  <div class="abs pdiv" style="left:507px"></div>
  <div class="abs partner" style="left:553px">
    <div class="pname" style="color:#c21a1a">Pembry Controls</div>
    <div class="pcap" style="padding-left:10px">Software Solutions</div>
  </div>
</section>

<footer>
  <div class="abs footer"></div>
  <div class="abs flinks"><span>HOME PAGE</span><span>SERVICES</span><span>CONTACT</span><span>ABOUT</span></div>
  <div class="abs copy">© 2015. VEL Engineering Solutions . All rights reserved.</div>
  <div class="abs pay"><span></span><span></span><span></span><span></span></div>
  <div class="abs social"><span style="background:#3b5ea8"></span><span style="background:#29a9e0"></span><span style="background:#1d6fa8"></span><span style="background:#e2841a"></span></div>
  <div class="abs c4">C4</div>
  <div class="abs footline"></div>
</footer>
</body>
</html>
```